Medical Software Informational Flyer and Website Design

Our company, Copper Fern Systems, is launching a new product, the CFS Clinic Workflow Hub. It is a software suite that will increase the productivity and volume of a LASIK practice.

We want this flyer to be a companion to our big reveal presentation at VEG and BLUDO; it's primary purpose is to inform potential clients on the many ways this software will help their practice. It is also obviously a promotional material. Because it is a companion to our presentation, we feel that it is acceptable for the flyer to contain much more text than would normally be reasonable in a flyer; it will go into more detail about the 12 major selling points of our software than our presentation time will allow. Having said that, however, we still want there to be "breathing room" for the design and the viewer's eyes.

We have uploaded our logo, both in full color and in white with no background (often used for watermarks, but certainly not restricted for that use alone). Our logo should be accompanied by either "Copper Fern Systems" or "CFS" using the Trajan Pro font (unoriginal, we know, but it's what we've chosen). We have included a color palette that compliments our logo, but designs are not limited to that palette (for example, we have found a pink (#cc1448) that compliments the palette and that we have used in the presentation).

We have also uploaded a PSD that includes icons that could compliment 9 of the 12 major selling points for the CFS Clinic Workflow Hub software (the category titles are subject to change). The icons are not necessarily set in stone. For consistency with our presentation, the Protection, Integration, and Review icons should be used, but any of the remaining six (in particular, the Personalized icon) can be changed to whatever you think might be more suitable. The PSD also has some preliminary text for a few of the 12 selling points (we are refining the text now and will get the final content to designers very soon). Also note that the font is simply a placeholder; use whatever font you think would best compliment your design. Finally, keep in mind that the PSD does NOT reflect a design we are looking for; in fact, we hate this "design" and hesitate to call it a design. It was simply a way to arrange the elements to easily distribute them to designers.

We want an 8 1/2in x 11in 8-page flyer that is professional, simple, and has a clear message: this product will revolutionize your practice! We of course also need a website design that compliments the flyer design once the flyer design is finalized and chosen.

We will be monitoring this project closely-- please ask any questions you have!
Updates

Target Market(s)

Physicians, technicians, and marketing personnel in the LASIK industry.

Industry/Entity Type

Software

Number of Pages Required

4 page

Font styles to use
Serif
Sans Serif

```html
<!DOCTYPE html>
<html lang="en">
<head>
<meta charset="utf-8">
<title>CFS Clinic Workflow Hub – Flyer</title>
<link rel="stylesheet" href="https://fonts.googleapis.com/css2?family=Cinzel:wght@400;600;700&family=Oswald:wght@600;700&family=Open+Sans:wght@400;600&display=swap">
<style>
  :root {
    --stage: #d9dbdc;
    --ink-dark: #0b1f22;
    --ink-band: #0e2024;
    --mint: #56c19a;
    --mint-light: #c6ecdc;
    --mint-line: #4cc39a;
    --back-deep: #081816;
    --back-mid: #133029;
    --paper-white: #ffffff;
    --band-text: #e6efec;
    --illus-orange: #f07a1e;
    --illus-blue: #1d5fa3;
    --illus-skin: #c9a08a;
  }
  * { box-sizing: border-box; margin: 0; padding: 0; }
  html, body { width: 1200px; height: 1098px; overflow: hidden; }
  body { background: var(--stage); position: relative; }

  .page {
    position: absolute;
    top: 153px;
    width: 560px;
    height: 791px;
    overflow: hidden;
    box-shadow: 0 6px 18px rgba(0,0,0,.25);
  }

  /* Front cover */
  .cover {
    left: 30px;
    background: radial-gradient(ellipse 60% 55% at 50% 55%, var(--mint-light) 0%, #8fd8b9 55%, var(--mint) 100%);
  }
  .cover-topband {
    position: absolute; top: 0; left: 0; right: 0; height: 24px;
    background: var(--ink-band);
  }
  .cover-headline {
    position: absolute; top: 36px; left: 0; right: 0;
    text-align: center;
    font-family: "Cinzel", serif;
    color: var(--ink-dark);
    line-height: 1;
  }
  .cover-headline .line-main { display: block; font-size: 45px; font-weight: 600; letter-spacing: 1px; }
  .cover-headline .line-sub { display: block; font-size: 30px; font-weight: 600; margin-top: 2px; }

  .cover-ribbon {
    position: absolute; top: 106px; left: 62px;
    width: 412px; height: 60px;
  }
  .cover-ribbon svg { position: absolute; inset: 0; }
  .cover-ribbon .ribbon-label {
    position: absolute; top: 12px; left: 24px;
    font-family: "Oswald", sans-serif;
    font-weight: 700;
    font-size: 26px;
    color: var(--ink-dark);
    transform: rotate(-2.2deg);
    transform-origin: left center;
    white-space: nowrap;
  }

  .product-art {
    position: absolute; top: 215px; left: 100px;
    width: 385px; height: 445px;
    background: linear-gradient(100deg, #a64a35 0%, var(--illus-orange) 18%, #f4b02a 30%, var(--illus-blue) 48%, var(--illus-skin) 70%, #e9d6ce 100%);
  }
  .product-shadow {
    position: absolute; top: 670px; left: 120px;
    width: 340px; height: 18px;
    background: radial-gradient(ellipse at center, rgba(0,0,0,.35) 0%, rgba(0,0,0,0) 70%);
  }

  .cover-footband {
    position: absolute; left: 0; right: 0; bottom: 0; height: 75px;
    background: var(--ink-band);
    border-bottom: 4px solid var(--mint-line);
    padding-top: 8px;
    text-align: center;
    font-family: "Cinzel", serif;
    font-size: 12px;
    color: var(--band-text);
    line-height: 18px;
    letter-spacing: .4px;
  }
  .cover-footband .sep { margin: 0 6px; }

  /* Back cover */
  .back {
    left: 610px;
    background: radial-gradient(ellipse 70% 60% at 45% 45%, var(--back-mid) 0%, var(--back-deep) 80%);
  }
  .back-frame {
    position: absolute;
    border: 1px solid rgba(160,190,180,.22);
  }
  .back-frame.f1 { top: -30px; left: -40px; width: 150px; height: 190px; transform: rotate(-10deg); }
  .back-frame.f2 { top: 40px; right: -30px; width: 120px; height: 260px; transform: rotate(-8deg); }
  .back-frame.f3 { bottom: 30px; right: -40px; width: 170px; height: 160px; transform: rotate(-10deg); }
  .back-frame.f4 { bottom: -20px; left: -20px; width: 100px; height: 180px; transform: rotate(-6deg); }

  .brand-mark {
    position: absolute; top: 140px; left: 0; right: 0;
    display: flex; align-items: center; justify-content: center; gap: 12px;
    font-family: "Cinzel", serif;
    font-weight: 600;
    font-size: 22px;
    color: var(--paper-white);
  }
  .brand-mark .brand-square {
    width: 22px; height: 22px;
    border: 3px solid var(--paper-white);
  }
  .contact {
    position: absolute; left: 0; right: 0;
    text-align: center;
    font-family: "Open Sans", sans-serif;
    color: var(--paper-white);
  }
  .contact.web { top: 362px; font-size: 17px; letter-spacing: 1.5px; }
  .contact.phone { top: 518px; font-size: 44px; color: var(--mint-line); letter-spacing: .5px; }
  .contact.email { top: 576px; font-size: 18px; letter-spacing: 1.2px; }
  .contact.address { top: 648px; font-size: 13px; }
</style>
</head>
<body>

<section class="page cover">
  <div class="cover-topband"></div>
  <h1 class="cover-headline">
    <span class="line-main">REVOLUTIONIZE</span>
    <span class="line-sub">YOUR PRACTICE!</span>
  </h1>
  <div class="cover-ribbon">
    <svg viewBox="0 0 412 60" width="412" height="60" aria-hidden="true">
      <polygon points="0,22 405,0 412,40 8,58 18,40" fill="#ffffff"/>
    </svg>
    <span class="ribbon-label">CFS Clinic Workflow Hub</span>
  </div>
  <div class="product-art" role="img" aria-label="Software box illustration with a close-up eye photograph and feature words"></div>
  <div class="product-shadow"></div>
  <footer class="cover-footband">
    <div>Connectivity<span class="sep">|</span>Personalized<span class="sep">|</span>Integration</div>
    <div>Protection<span class="sep">|</span>High Performance</div>
    <div>Word of Mouth<span class="sep">|</span>Reviews<span class="sep">|</span>Planning Tools<span class="sep">|</span>Improvement Tools</div>
  </footer>
</section>

<section class="page back">
  <div class="back-frame f1"></div>
  <div class="back-frame f2"></div>
  <div class="back-frame f3"></div>
  <div class="back-frame f4"></div>
  <div class="brand-mark"><span class="brand-square"></span>Copper Fern Systems</div>
  <p class="contact web">www.websiteHere@.com</p>
  <p class="contact phone">000-000-0000</p>
  <p class="contact email">Email Here:cfsMail_id_@.com</p>
  <p class="contact address">Address Here</p>
</section>

</body>
</html>
```